uk based ecommerce website requires fresh look ,high quality look and feel

we are a web based company selling eco friendly ground reinforcement grids to diy and construction sectors
our existing website is www.pondermeshpaths.co.uk ,

we have already updated the logo so that is the branding sorted .so we need a ecommerce website that is very much up-to date in design and layout and which has content management system for ease of use so that we can add products and information as required.

Use current logo as reference for colour scheme.
www.pondermeshpaths.co.uk

The current website has 6 pages accessible through the navigation bar, I would now like 5 pages, removing the need for the Trade Enquiries page possibly have it with along with contact us.

Target Market(s)

construction industry , diy end users,
retail market, landscapers, gardeners

Industry/Entity Type

Construction

Font styles to use
Other font styles liked:
• logo font prometo

Colors
f78f20
9bcb3c

Requirements
Must have
• logo colours and logo design in website with cms responsive design for tablet and mobile devices
• expect content to work flawlessly and look great across all devices
• HTML 5 custom design with coding as required
• must have good experiance in ecommerce website design
• eye catching, high quality look and feel and very user friedly ,very up-to date.
Nice to have
• picture slider show
• explain in writing what exactly i am getting in my ecommerce website
Should not have
• plain , basic design , old fashion looking ,cheap look

```html
<!DOCTYPE html>
<html lang="en">
<head>
<meta charset="utf-8">
<title>PonderMesh Ground Solutions – Ground Solutions</title>
<link rel="stylesheet" href="https://fonts.googleapis.com/css2?family=Open+Sans:wght@300;400;600&display=swap">
<style>
:root{
  --orange:#f78f20;
  --green:#9bcb3c;
  --dark:#2b2b2b;
  --darker:#222;
  --band:#f2f2f2;
  --text:#555;
  --heading:#222;
  --white:#fff;
}
*{box-sizing:border-box;margin:0;padding:0}
html,body{width:1200px;height:1106px;overflow:hidden}
body{font-family:"Open Sans",Arial,sans-serif;color:var(--text);background:var(--white);position:relative}
a{color:inherit;text-decoration:none}
.topbar{position:absolute;left:0;top:0;width:1200px;height:35px;background:var(--dark);color:var(--white);font-size:12px}
.topbar .phones{position:absolute;left:89px;top:9px;display:flex;align-items:center}
.topbar .phones svg{margin-right:7px}
.topbar .sep{width:1px;height:17px;background:#aaa;margin:0 12px}
.topbar .account{position:absolute;right:89px;top:9px;display:flex;align-items:center;gap:5px}
.topbar .account svg{margin-left:12px}
.header{position:absolute;left:0;top:35px;width:1200px;height:75px}
.brand{position:absolute;left:89px;top:5px;display:flex;align-items:center;gap:10px}
.brand .mark{width:46px;height:46px;border-radius:50%;background:var(--green)}
.brand .name{font-size:16px;font-weight:600;color:var(--orange);line-height:1.1}
.brand .name small{display:block;font-size:10px;letter-spacing:.5px}
.nav{position:absolute;right:140px;top:0;height:75px;display:flex;gap:18px;font-size:11.5px;color:#333;white-space:nowrap}
.nav a{display:block;padding-top:34px;position:relative}
.nav a.active::before{content:"";position:absolute;left:-14px;right:-14px;top:0;height:3px;background:var(--orange)}
.cart{position:absolute;right:89px;top:21px;width:34px;height:34px;border-radius:50%;background:var(--orange);display:flex;align-items:center;justify-content:center}
.pagetitle{position:absolute;left:0;top:110px;width:1200px;height:70px;background:var(--band)}
.pagetitle h1{position:absolute;left:89px;top:19px;font-size:27px;font-weight:400;color:var(--heading)}
.crumbs{position:absolute;right:89px;top:28px;font-size:12px;color:#333}
.frame{position:absolute;border:3px solid var(--orange)}
.photo{position:absolute}
.photo.drive{left:101px;top:231px;width:302px;height:226px;background:linear-gradient(180deg,#3c4148 0%,#6a6d70 35%,#9a9a98 70%,#b4b3b0 100%)}
.photo.person{left:787px;top:536px;width:301px;height:226px;background:linear-gradient(90deg,#f0efec 0%,#e4ddd6 40%,#b08f7c 70%,#5a3a2c 100%)}
.intro{position:absolute;left:419px;top:212px;width:690px}
.intro h2{font-size:25px;font-weight:400;color:var(--heading);margin-bottom:8px}
.intro h2 span{color:var(--orange)}
.intro p{font-size:11px;line-height:19.5px;margin:0 0 9px 3px}
.enquiry{position:absolute;right:437px;top:522px;width:620px;text-align:right}
.enquiry h2{font-size:24px;font-weight:400;color:var(--heading)}
.enquiry .call{font-size:18px;font-weight:300;color:var(--orange);margin:7px 6px 9px 0}
.enquiry p{font-size:11px;line-height:22px;width:425px;margin-left:auto}
.footer{position:absolute;left:0;top:820px;width:1200px;height:238px;background:var(--dark);color:#eee}
.footer .col{position:absolute;top:32px}
.footer h3{font-size:15px;font-weight:400;color:var(--white);padding-bottom:10px;position:relative;margin-bottom:17px}
.footer h3::after{content:"";position:absolute;left:0;bottom:0;width:29px;height:2px;background:var(--orange)}
.about p{font-size:11.5px;line-height:19.6px;width:240px}
.cards{display:flex;gap:6px;margin-top:13px}
.cards span{width:58px;height:32px;border-radius:2px;background:#f4f4f4}
.cards span:nth-child(2){background:#1c3f8d}
.cards span:nth-child(3){background:#111}
.cards span:nth-child(4){background:#f7ecd0}
.links li{list-style:none;font-size:11.5px;line-height:24px}
.touch .row{display:flex;align-items:center;font-size:13px;margin-bottom:13px}
.touch .ico{width:28px;height:28px;background:var(--orange);display:flex;align-items:center;justify-content:center;margin-right:8px}
.newsletter .email{width:229px;height:37px;background:var(--white);color:#777;font-size:12px;padding:10px 12px}
.newsletter .send{width:113px;height:35px;background:var(--orange);color:var(--white);font-size:12px;text-align:center;line-height:35px;margin-top:8px}
.bottombar{position:absolute;left:0;top:1058px;width:1200px;height:48px;background:var(--darker);color:var(--white);font-size:12px;padding:23px 0 0 92px}
.totop{position:absolute;z-index:2;left:1068px;top:1036px;width:48px;height:48px;border-radius:50%;background:var(--white);border:1px solid #ddd;display:flex;align-items:center;justify-content:center}
</style>
</head>
<body>
<div class="topbar">
  <div class="phones">
    <svg width="14" height="14" viewBox="0 0 24 24"><path fill="#fff" d="M6.6 10.8a15 15 0 0 0 6.6 6.6l2.2-2.2c.3-.3.7-.4 1-.2 1.1.4 2.3.6 3.6.6.6 0 1 .4 1 1V20c0 .6-.4 1-1 1A17 17 0 0 1 3 4c0-.6.4-1 1-1h3.5c.6 0 1 .4 1 1 0 1.3.2 2.5.6 3.6.1.3 0 .7-.2 1z"/></svg>
    <span>0147-555-0192</span><span class="sep"></span><span>0845-555-0137</span>
  </div>
  <div class="account"><a href="#">Login</a><span>|</span><a href="#">Register</a>
    <svg width="13" height="13" viewBox="0 0 24 24"><circle cx="10" cy="10" r="7" fill="none" stroke="#fff" stroke-width="2.5"/><path d="M15 15l7 7" stroke="#fff" stroke-width="2.5"/></svg>
  </div>
</div>

<header class="header">
  <div class="brand"><span class="mark"></span><span class="name">PONDERMESH<small>GROUND SOLUTIONS</small></span></div>
  <nav class="nav">
    <a href="#" class="active">SHOP</a><a href="#">ABOUT US</a><a href="#">GROUND SOLUTIONS</a><a href="#">PONDERMESH</a><a href="#">CONTACT US</a>
  </nav>
  <a class="cart" href="#" aria-label="Cart"><svg width="18" height="18" viewBox="0 0 24 24"><path fill="#fff" d="M7 18a2 2 0 1 0 0 4 2 2 0 0 0 0-4zm10 0a2 2 0 1 0 0 4 2 2 0 0 0 0-4zM1 2h3.3l.9 2H21c.6 0 1 .6.8 1.2l-3.3 6c-.3.5-.9.8-1.5.8H8.1l-.9 1.7V14h12v2H7c-1.1 0-1.9-1.2-1.4-2.2L7 11.1 3.3 4H1z"/></svg></a>
</header>

<div class="pagetitle">
  <h1>Ground Solutions</h1>
  <div class="crumbs">Home / Ground Solutions</div>
</div>

<div class="frame" style="left:89px;top:216px;width:302px;height:258px"></div>
<div class="photo drive" role="img" aria-label="Photo of a car wheel parked on a grey gravel driveway"></div>
<section class="intro">
  <h2>Gravel <span>Driveways</span></h2>
  <p>Gravel driveways are one of the most popular choices for driveways and hard landscaping in the UK and it's easy to see why. It's cost effective, low maintenance and looks great particularly in rural settings or in town where it matches the predominant stone and brick colouring of the area.</p>
  <p>There is an immense choice of size, colours and shapes available, making it an excellent choice for resurfacing. Gravel is also a very good deterrent against any kind of burglary as it makes a crunching noise as you walk over the surface, making it not a favorite amongst the undesirables of our society.</p>
  <p>The combination of gravel and our Cellular ground reinforcement grid system's makes the perfect choice for the modern driveway or path. Incorporating the tried and tested gravel driveway and combining with the holding chambers of the ground reinforce-ment system. This will not be moving around like the normal gravel driveway which makes it the perfect choice. This system does not require planning permission as it is free draining allowing water back into the ground &nbsp;replenishing instead of putting strain on our street drainage systems.</p>
</section>

<section class="enquiry">
  <h2>All enquiries by email on our contact page or by</h2>
  <div class="call">Calling on : 0845-555-0137</div>
  <p>Our If you feel this is the best choice for you then go to our online store and buy with confidence because this is a light-weight eco-friendly and which is easy to handle and so simple to lay system.</p>
</section>
<div class="frame" style="left:798px;top:521px;width:303px;height:258px"></div>
<div class="photo person" role="img" aria-label="Photo of a smiling customer service representative"></div>

<footer class="footer">
  <div class="col about" style="left:92px">
    <h3>About Us</h3>
    <p>Lorem Ipsum is simply dummy text of the printing and typesetting industry. Lorem Ipsum has been the industry's standard dummy text ever since the 1500s</p>
    <div class="cards" aria-label="Accepted payment methods"><span></span><span></span><span></span><span></span></div>
  </div>
  <div class="col links" style="left:397px">
    <h3>Useful Links</h3>
    <ul><li>Site Map</li><li>Email</li><li>Privacy Policy</li><li>Terms of Service</li><li>Delivery and Returns</li></ul>
  </div>
  <div class="col touch" style="left:597px">
    <h3>Get In Touch</h3>
    <div class="row"><span class="ico"><svg width="12" height="12" viewBox="0 0 24 24"><path fill="#fff" d="M6.6 10.8a15 15 0 0 0 6.6 6.6l2.2-2.2c.3-.3.7-.4 1-.2 1.1.4 2.3.6 3.6.6.6 0 1 .4 1 1V20c0 .6-.4 1-1 1A17 17 0 0 1 3 4c0-.6.4-1 1-1h3.5c.6 0 1 .4 1 1 0 1.3.2 2.5.6 3.6.1.3 0 .7-.2 1z"/></svg></span>0147-555-0192</div>
    <div class="row"><span class="ico"><svg width="13" height="10" viewBox="0 0 26 20"><rect x="1" y="1" width="24" height="18" fill="none" stroke="#fff" stroke-width="2"/><path d="M1 1l12 10 12-10" fill="none" stroke="#fff" stroke-width="2"/></svg></span>sales@pondermeshpaths.co.uk</div>
  </div>
  <div class="col newsletter" style="left:871px">
    <h3>Newsletter</h3>
    <div class="email">Email</div>
    <div class="send">SEND</div>
  </div>
</footer>
<div class="bottombar">© 2016 All Rights Reserved</div>
<a class="totop" href="#" aria-label="Back to top"><svg width="12" height="8" viewBox="0 0 12 8"><path d="M1 7l5-5 5 5" fill="none" stroke="#f78f20" stroke-width="2"/></svg></a>
</body>
</html>
```